Brightmill Data Works

Our company is about IT hardwares and IT solutions. IT hardware such as PC, RAMS, storage and servers. IT solutions such as project management, BA. We are also selling new technology too.

Target Market(s)

Consumer, Small to Medium Business, Corporate

Requirements
Must have
• The business card must have the following:
• Name:
• Title:
• Contact Number:
• Email address:
• Website:
• Color: Must match the logo color upgrade

```html
<!DOCTYPE html>
<html lang="en">
<head>
<meta charset="utf-8">
<title>Brightmill Data Works – Business Card</title>
<link href="https://fonts.googleapis.com/css2?family=Work+Sans:wght@400;500;600&display=swap" rel="stylesheet">
<style>
  :root {
    --stage: #161616;
    --card: #1f1f1f;
    --card-edge: #2a2a2a;
    --silver: #d9d9d9;
    --silver-dim: #b8b8b8;
    --embossed: #3a3a3a;
    --rule: #6e6e6e;
  }
  * { margin: 0; padding: 0; box-sizing: border-box; }
  html, body {
    width: 1200px;
    height: 900px;
    overflow: hidden;
    background: var(--stage);
    font-family: "Work Sans", sans-serif;
  }
  .canvas {
    position: relative;
    width: 1200px;
    height: 900px;
    background: radial-gradient(ellipse at 60% 40%, #222 0%, var(--stage) 70%);
  }
  .card {
    position: absolute;
    left: 240px;
    width: 720px;
    height: 410px;
    background: var(--card);
    border: 1px solid var(--card-edge);
    box-shadow: 0 12px 30px rgba(0,0,0,0.6);
  }
  .card--front { top: 40px; }
  .card--back { top: 470px; }

  .brand {
    display: flex;
    align-items: center;
    gap: 14px;
    font-weight: 600;
    letter-spacing: 0.04em;
    text-transform: uppercase;
  }
  .brand__mark {
    width: 22px;
    height: 22px;
    background: currentColor;
  }
  .card--front .brand {
    position: absolute;
    inset: 0;
    justify-content: center;
    font-size: 40px;
    color: var(--silver);
  }

  .card--back .brand {
    position: absolute;
    left: 50px;
    top: 0;
    height: 100%;
    width: 330px;
    justify-content: center;
    font-size: 25px;
    color: var(--embossed);
  }
  .card--back .brand__mark { width: 16px; height: 16px; flex: none; }

  .divider {
    position: absolute;
    left: 410px;
    top: 95px;
    width: 1px;
    height: 220px;
    background: var(--rule);
  }

  .details {
    position: absolute;
    left: 440px;
    top: 95px;
    color: var(--silver);
  }
  .details__name {
    font-size: 25px;
    font-weight: 500;
    letter-spacing: 0.03em;
    text-transform: uppercase;
    line-height: 1;
  }
  .details__title {
    font-size: 15px;
    color: var(--silver-dim);
    margin-top: 4px;
  }
  .details__address {
    font-size: 16px;
    line-height: 1.35;
    margin-top: 18px;
    font-style: normal;
  }
  .contacts {
    list-style: none;
    margin-top: 16px;
    font-size: 16px;
    line-height: 1.5;
  }
  .contacts li {
    display: flex;
    align-items: center;
    gap: 9px;
  }
  .contacts svg {
    width: 12px;
    height: 12px;
    flex: none;
    stroke: var(--silver);
    fill: none;
    stroke-width: 1.6;
  }
</style>
</head>
<body>
<main class="canvas">
  <section class="card card--front">
    <div class="brand"><span class="brand__mark"></span>Brightmill Data Works</div>
  </section>

  <section class="card card--back">
    <div class="brand"><span class="brand__mark"></span>Brightmill Data Works</div>
    <div class="divider"></div>
    <div class="details">
      <p class="details__name">Daniel Reyes</p>
      <p class="details__title">Director</p>
      <address class="details__address">2250 Orchard Vale Rd<br>Lindell, CA 95012-4410</address>
      <ul class="contacts">
        <li>
          <svg viewBox="0 0 12 12"><path d="M2.5 1.5l2 2-1 1.2c.6 1.4 1.6 2.4 3 3l1.2-1 2 2-1.4 1.6C4.8 10 2 7.2 1.2 3.4z"/></svg>
          555-204-7731
        </li>
        <li>
          <svg viewBox="0 0 12 12"><rect x="1" y="2.5" width="10" height="7"/><path d="M1 2.5l5 4 5-4"/></svg>
          info@brightmilldata.com
        </li>
        <li>
          <svg viewBox="0 0 12 12"><circle cx="6" cy="6" r="5"/><ellipse cx="6" cy="6" rx="2.2" ry="5"/><path d="M1 6h10"/></svg>
          www.brightmilldata.com
        </li>
      </ul>
    </div>
  </section>
</main>
</body>
</html>
```